MBR - Stationery Design Project

We need stationery based on our logo.

Company info :
Cabinet Voisard & Associés
Société à responsabilité limitée au capital de 200.000 FCFP
RCS Papeete 27586K - Numéro tahiti K73962
Centre d’affaires OPALE - Rue Gaston Perrin
BP 61384 MAHU POTE - 98752 Papeete
Tahiti - Polynésie française
Tél : +689 40 73 16 48
Fax : +689 40 39 64 91

Industry/Entity Type

It Company

Font styles to use
Sans Serif

```html
<!DOCTYPE html>
<html lang="fr">
<head>
<meta charset="utf-8">
<title>MBR – Cartes de visite</title>
<link href="https://fonts.googleapis.com/css2?family=Jost:wght@300;400&display=swap" rel="stylesheet">
<style>
  :root {
    --backdrop: #e4e4e6;
    --card: #ffffff;
    --navy: #1f3659;
    --slate: #8c9c9c;
    --rule: #b9c2c4;
  }
  html, body {
    margin: 0;
    width: 1200px;
    height: 1000px;
    overflow: hidden;
    background: var(--backdrop);
    font-family: "Jost", "Century Gothic", sans-serif;
  }
  .stage {
    position: relative;
    width: 1200px;
    height: 1000px;
  }
  .card {
    position: absolute;
    left: 300px;
    width: 600px;
    height: 343px;
    background: var(--card);
    box-shadow: 0 6px 18px rgba(0,0,0,0.12);
    box-sizing: border-box;
  }
  .card--front { top: 110px; display: flex; align-items: center; justify-content: center; }
  .card--back  { top: 540px; }

  .brand { color: var(--navy); }
  .brand__mark {
    display: block;
    font-weight: 300;
    line-height: 0.9;
    letter-spacing: 2px;
  }
  .brand__name {
    display: block;
    font-weight: 400;
    white-space: nowrap;
  }
  .brand__tagline {
    display: block;
    color: var(--slate);
    font-weight: 300;
    white-space: nowrap;
  }

  .card--front .brand { text-align: left; }
  .card--front .brand__mark { font-size: 112px; }
  .card--front .brand__name { font-size: 24px; margin-top: 6px; }
  .card--front .brand__tagline { font-size: 12.5px; margin-top: 2px; letter-spacing: 0.3px; }

  .card--back .brand { position: absolute; left: 32px; top: 34px; }
  .card--back .brand__mark { font-size: 50px; }
  .card--back .brand__name { font-size: 11px; margin-top: 3px; }
  .card--back .brand__tagline { font-size: 6.5px; margin-top: 1px; }

  .contact-person {
    position: absolute;
    right: 34px;
    top: 74px;
    text-align: right;
  }
  .contact-person__name {
    margin: 0;
    font-size: 30px;
    font-weight: 300;
    color: var(--navy);
  }
  .contact-person__title {
    margin: 4px 0 0;
    padding-top: 4px;
    border-top: 1px solid var(--rule);
    font-size: 17px;
    font-weight: 300;
    color: var(--slate);
  }

  .address {
    position: absolute;
    left: 150px;
    right: 34px;
    bottom: 58px;
    border-top: 1px solid var(--rule);
    padding-top: 8px;
    text-align: right;
    font-style: normal;
    font-size: 11px;
    line-height: 1.6;
    color: var(--navy);
    font-weight: 300;
  }
  .address span { display: block; white-space: nowrap; }
</style>
</head>
<body>
<main class="stage">
  <section class="card card--front" aria-label="Carte de visite, recto">
    <div class="brand">
      <span class="brand__mark">MBR</span>
      <span class="brand__name">Cabinet Voisard &amp; Associés</span>
      <span class="brand__tagline">Expertise-comptable · Audit · Conseil</span>
    </div>
  </section>

  <section class="card card--back" aria-label="Carte de visite, verso">
    <div class="brand">
      <span class="brand__mark">MBR</span>
      <span class="brand__name">Cabinet Voisard &amp; Associés</span>
      <span class="brand__tagline">Expertise-comptable · Audit · Conseil</span>
    </div>

    <div class="contact-person">
      <p class="contact-person__name">Marc Tessier</p>
      <p class="contact-person__title">Managing Director</p>
    </div>

    <address class="address">
      <span>Centre d’affaires OPALE - Rue Gaston Perrin BP 61384 MAHU POTE - 98752 Papeete, Tahiti</span>
      <span>Tél : +689 40 73 16 48 | Fax : +689 40 39 64 91</span>
    </address>
  </section>
</main>
</body>
</html>
```